jewellery store flyer

Front to show
-company name and logo
underneath of company name, I want " The perfect creation" to be written.
-background bright tone jewellery or model wearing jewellery(prefer engagement and wedder or wedder set)

--------------------------------------------------------------
Back to show list of service and brief map of location
with addresss and contact detail

introducing newly established jewellery store with exclusive and unique jewellery. We offer you
-specialized in hand made jewellery
-on site jeweller and designer
-repair and restoring
-laser engraving and laser solder

5/41 Marrowind Crescent Griffith ACT 2603
02) 6174 3019
Enquiry: tansy.r@mailvane.com
---------------------------------------------------------------------
I have enclosed mockups that I made by myself, to show what I was thinking. this is just for reference. New flyer doesn't need to look the same.

I don't mind either holizontal nor vertical.
I don't mind if you add text or remove text that I have written above.
I want flyer to look morden and neat.

Good luck to you & me and enjoy creation.
Kind regards,
Petra

Target Market(s)

introducing newly established store.
aiming for engagement & wedding rings and remakes

Industry/Entity Type

It Company

Font styles to use
Other font styles liked:
• Monotype corsive for script but name and address for SERIF

Colors

Designer to choose colors to be used in the design.

Requirements
Must have
• background photo including jewellery
• company name and address
• service detail
Nice to have
• brief map of location( I have red circled few places that people know more on the map I attached here.)
• Map to be simplified please.
• Please do not use Google map directly.
• Opening hours: Mon-Fri 9.30 to 5.30 Sat 10.00 to 5

```html
<!DOCTYPE html>
<html lang="en">
<head>
<meta charset="utf-8">
<title>Fernleaf Jewellery – Flyer</title>
<link href="https://fonts.googleapis.com/css2?family=Cinzel:wght@600&family=Sorts+Mill+Goudy&display=swap" rel="stylesheet">
<style>
  :root {
    --backdrop: #5f6064;
    --paper: #ffffff;
    --ink: #231f20;
    --ink-soft: #333132;
    --band: #231f20;
    --band-text: #ffffff;
    --map-fill: #d7dae1;
    --map-street: #f2f3f6;
    --photo-light: #f3f3f3;
    --photo-mid: #e4dfda;
    --photo-warm: #c9ada0;
    --photo-dark: #3a3536;
  }
  * { box-sizing: border-box; margin: 0; padding: 0; }
  html, body {
    width: 1200px; height: 828px; overflow: hidden;
    background: var(--backdrop);
  }
  body {
    font-family: "Sorts Mill Goudy", Georgia, serif;
    font-variant-numeric: lining-nums;
    color: var(--ink);
    position: relative;
  }
  .flyer {
    position: absolute; left: 119px; top: 93px;
    width: 962px; height: 641px;
    background: var(--paper);
    overflow: hidden;
  }
  .hero-photo {
    position: absolute; left: 0; top: 0; width: 962px; height: 269px;
    background: linear-gradient(90deg, var(--photo-light) 0%, #ededed 38%, var(--photo-mid) 55%, var(--photo-warm) 72%, #d9cfc8 86%, var(--photo-dark) 100%);
  }
  .brand-name {
    position: absolute; left: 78px; top: 158px;
    font-family: "Cinzel", "Sorts Mill Goudy", serif;
    font-weight: 600;
    font-size: 38px; line-height: 1;
    letter-spacing: 0;
    color: var(--ink);
  }
  .intro {
    position: absolute; left: 45px; top: 306px;
    font-size: 22.5px; line-height: 30px;
    color: var(--ink-soft);
  }
  .offer-title {
    position: absolute; left: 45px; top: 392px;
    font-size: 22px; font-weight: bold; color: var(--ink);
  }
  .services {
    position: absolute; left: 43px; top: 431px;
    list-style: none;
  }
  .services li {
    display: flex; align-items: center; gap: 14px;
    font-size: 22.5px; line-height: 29px; color: var(--ink-soft);
  }
  .services svg { width: 18px; height: 18px; flex: none; }
  .location-map {
    position: absolute; left: 500px; top: 287px;
    width: 390px; height: 160px;
    background: linear-gradient(160deg, var(--map-fill) 0%, var(--map-fill) 30%, var(--map-street) 42%, var(--map-fill) 55%, var(--map-fill) 100%);
  }
  .contact {
    position: absolute; left: 497px; top: 461px;
    font-size: 20px; line-height: 24px; color: var(--ink-soft);
  }
  .contact-row { display: flex; align-items: flex-start; gap: 9px; margin-bottom: 8px; }
  .contact-row svg { width: 24px; height: 24px; flex: none; }
  .contact-row strong { color: var(--ink); }
  .social {
    position: absolute; left: 826px; top: 550px;
    display: flex; gap: 8px;
  }
  .social span {
    width: 35px; height: 35px; border-radius: 50%;
    background: var(--band); display: block;
  }
  .tagline-band {
    position: absolute; left: 0; bottom: 0; width: 962px; height: 46px;
    background: var(--band);
    color: var(--band-text);
    font-size: 20.5px; font-weight: bold; letter-spacing: 0.2px;
    text-transform: uppercase;
    display: flex; align-items: center; justify-content: center;
    padding-right: 30px;
  }
</style>
</head>
<body>
  <main class="flyer">
    <div class="hero-photo" role="img" aria-label="Photograph of a bride in a veil with pearl earrings and a groom in a dark suit, foreheads touching"></div>
    <h1 class="brand-name">Fernleaf Jewellery</h1>

    <p class="intro">Introducing newly established jewellery<br>store with exclusive and unique jewellery.</p>
    <h2 class="offer-title">We offer you:</h2>
    <ul class="services">
      <li><svg viewBox="0 0 18 18"><circle cx="9" cy="9" r="7.6" fill="none" stroke="#231f20" stroke-width="1.5"/><path d="M7.5 5.5 L11 9 L7.5 12.5" fill="none" stroke="#231f20" stroke-width="2"/></svg>Specialized in hand made jewellery</li>
      <li><svg viewBox="0 0 18 18"><circle cx="9" cy="9" r="7.6" fill="none" stroke="#231f20" stroke-width="1.5"/><path d="M7.5 5.5 L11 9 L7.5 12.5" fill="none" stroke="#231f20" stroke-width="2"/></svg>On site jeweller and designer</li>
      <li><svg viewBox="0 0 18 18"><circle cx="9" cy="9" r="7.6" fill="none" stroke="#231f20" stroke-width="1.5"/><path d="M7.5 5.5 L11 9 L7.5 12.5" fill="none" stroke="#231f20" stroke-width="2"/></svg>Repair and restoring</li>
      <li><svg viewBox="0 0 18 18"><circle cx="9" cy="9" r="7.6" fill="none" stroke="#231f20" stroke-width="1.5"/><path d="M7.5 5.5 L11 9 L7.5 12.5" fill="none" stroke="#231f20" stroke-width="2"/></svg>Laser engraving and laser solder</li>
    </ul>

    <div class="location-map" role="img" aria-label="Simplified street map of Griffith showing the store on Marrowind Crescent near local landmarks"></div>

    <div class="contact">
      <div class="contact-row">
        <svg viewBox="0 0 24 24"><circle cx="12" cy="12" r="10.8" fill="none" stroke="#231f20" stroke-width="1.4"/><path d="M12 18.5 C9 14.5 8 12.5 8 10.5 a4 4 0 0 1 8 0 c0 2 -1 4 -4 8z" fill="#231f20"/><circle cx="12" cy="10.5" r="1.5" fill="#fff"/></svg>
        <span>5/41 Marrowind Crescent Griffith Canberra,<br>Australian Capital Territory ACT 2603</span>
      </div>
      <div class="contact-row">
        <svg viewBox="0 0 24 24"><circle cx="12" cy="12" r="10.8" fill="none" stroke="#231f20" stroke-width="1.4"/><rect x="6.5" y="8" width="11" height="8" fill="none" stroke="#231f20" stroke-width="1.4"/><path d="M6.5 8 L12 12.5 L17.5 8" fill="none" stroke="#231f20" stroke-width="1.4"/></svg>
        <span><strong>Enquiry:</strong> tansy.r@mailvane.com</span>
      </div>
      <div class="contact-row">
        <svg viewBox="0 0 24 24"><circle cx="12" cy="12" r="10.8" fill="none" stroke="#231f20" stroke-width="1.4"/><path d="M9 6.5 l2 2.5 -1.3 1.5 c0.8 1.8 2 3 3.8 3.8 l1.5 -1.3 2.5 2 -1.3 2 c-4 -0.3 -8 -4.3 -8.3 -8.3z" fill="#231f20"/></svg>
        <span><strong>+61 6174 3019</strong></span>
      </div>
    </div>

    <div class="social" aria-hidden="true"><span></span><span></span><span></span></div>

    <footer class="tagline-band">Our team will make a perfect piece as you dreamed !</footer>
  </main>
</body>
</html>
```